Wilderness Doc & TV personality personal page

I’m a wilderness and EMS emergency physician with particular sub specialties and a TV show. I need a website to highlight my interviews, teachings, etc... I did buy a number of domains for now.
Topics and things I need: CV (or version) me in the media, picture gallery, actually I sort of really like what dr owen barkley, my colleague has setup plus I have tv show and stuff like that. ridgeway healer dot com

Target Market(s)

EMS, education, commercial products...

Industry/Entity Type

Medical And Science

Coding

Coded - Design and coding required

Number of Pages Required

1 page

Font styles to use
Sans Serif

Colors
f37122
9bcb3c
0556a4
a54499

Requirements
Must have
• Links and photos to news articles and things that mention me that I can add in.
Nice to have
• Maybe some snapshots of lecture reviews or patient thank you notes. Accolades so to speak
• I really appreciate how sharp it is. I would love to see Headings that resemble my friend's at ridgeway healer dot com. Home, experience, consulting, lectures, affiliates, contact... those are main subjects... I think media also and that will have the TV show stuff and articles written about me...then maybe at the bottom of main page also have splits for training, research, television, and maybe exploration
Should not have
• The medical symbol with two snakes... that means quack doctor

```html
<!DOCTYPE html>
<html lang="en">
<head>
<meta charset="utf-8">
<title>Leo Marsh – Wilderness Doc</title>
<link href="https://fonts.googleapis.com/css2?family=Roboto+Slab:wght@400;700&family=Roboto:wght@400;500&display=swap" rel="stylesheet">
<style>
:root{
  --orange:#f37122;
  --green:#9bcb3c;
  --dark:#2d2d2d;
  --text:#555;
  --beige:#eedcc3;
  --white:#fff;
}
*{box-sizing:border-box;margin:0;padding:0}
html,body{width:1200px;height:3424px;overflow:hidden;background:var(--white)}
body{font-family:"Roboto",sans-serif;color:var(--text);position:relative}
.slab{font-family:"Roboto Slab",serif}
.photo{position:absolute}
.btn{display:inline-block;font-family:"Roboto",sans-serif;font-size:15px;font-weight:500;padding:14px 26px;border-radius:30px;background:var(--orange);color:var(--white);text-decoration:none}
.btn-outline{background:transparent;border:2px solid var(--white)}
.rule{width:60px;height:3px;background:var(--orange);margin-bottom:20px}
.rule-white{background:var(--white)}
p.body{font-size:15px;line-height:1.75}

/* header */
.site-header{position:absolute;top:0;left:0;width:1200px;height:104px;background:var(--white)}
.brand{position:absolute;left:112px;top:26px;font-family:"Roboto Slab",serif;font-size:40px;color:var(--orange)}
.main-nav{position:absolute;right:112px;top:36px;display:flex;gap:8px}
.main-nav a{font-size:15px;color:var(--dark);text-decoration:none;padding:10px 14px}
.main-nav a.active{border:1px solid #ccc;box-shadow:0 2px 6px rgba(0,0,0,.12);color:var(--orange)}

/* hero */
.hero{position:absolute;top:104px;left:0;width:1200px;height:680px;background:var(--beige);overflow:hidden}
.hero-photo{left:0;top:0;width:640px;height:680px;background:linear-gradient(135deg,#8e7b67,#c9a98a 55%,#e6d3bd)}
.hero-copy{position:absolute;left:660px;top:120px;width:440px}
.hero-title{font-family:"Roboto Slab",serif;font-size:62px;color:var(--orange);margin-bottom:22px}
.hero-copy p{margin-bottom:28px;color:#6a5a4a}
.hero-wave{position:absolute;left:0;bottom:0}

/* about */
.about{position:absolute;top:784px;left:0;width:1200px;height:530px}
.about-copy{position:absolute;left:112px;top:60px;width:500px}
.section-title{font-family:"Roboto Slab",serif;font-size:34px;color:var(--dark);margin-bottom:14px;font-weight:400}
.section-title span{color:var(--orange)}
.about-copy p{margin-bottom:18px}
.about-portrait{position:absolute;left:670px;top:70px;width:300px;height:300px;border-radius:50%;border:6px solid var(--orange);background:radial-gradient(circle at 50% 40%,#c49a78,#6b4a36)}

/* split sections */
.split{position:absolute;left:0;width:1200px;height:440px}
.tv{top:1314px}
.tv .photo{left:0;top:0;width:600px;height:440px;background:linear-gradient(135deg,#5b6470,#a79382 60%,#3e3a36)}
.panel{position:absolute;top:0;width:600px;height:440px;padding:60px 56px}
.panel-orange{left:600px;background:var(--orange);color:var(--white)}
.panel-green{left:0;background:var(--green);color:var(--white);padding-left:112px}
.panel .section-title{color:var(--white)}
.panel p{margin-bottom:26px;color:var(--white)}

/* gallery */
.gallery{position:absolute;top:1790px;left:0;width:1200px;height:380px;text-align:center}
.gallery .section-title{margin-top:20px}
.gallery .rule{margin:0 auto 40px}
.gallery-grid{position:absolute;left:110px;top:110px;display:flex;gap:15px}
.gallery-grid .photo{position:static;width:232px;height:230px}
.g1{background:linear-gradient(135deg,#8fa5b8,#4d5a66)}
.g2{background:linear-gradient(135deg,#7a6a58,#c8b39a)}
.g3{background:linear-gradient(135deg,#3d4a5c,#9c8a7a)}
.g4{background:linear-gradient(135deg,#36302c,#8a6a4e)}

.interviews{top:2190px}
.interviews .photo{left:600px;top:0;width:600px;height:440px;background:linear-gradient(135deg,#2f3038,#8a6f58 55%,#c9a27e)}

/* media */
.media{position:absolute;top:2660px;left:0;width:1200px;height:470px}
.media .photo{left:112px;top:40px;width:410px;height:380px;background:linear-gradient(135deg,#4e5c6a,#7d8c99 50%,#2e3640)}
.media-copy{position:absolute;left:672px;top:60px;width:420px}
.media-copy p{margin-bottom:26px}

/* footer */
.site-footer{position:absolute;top:3144px;left:0;width:1200px;height:280px;background:var(--dark);text-align:center;color:var(--white)}
.footer-brand{font-family:"Roboto Slab",serif;font-size:40px;color:var(--orange);margin-top:42px}
.footer-nav{margin-top:34px;font-size:15px}
.footer-nav a{color:var(--white);text-decoration:none;padding:0 18px}
.footer-nav .sep{color:#aaa}
.copyright{margin-top:30px;font-size:13px;color:#ccc}
</style>
</head>
<body>

<header class="site-header">
  <div class="brand">Leo Marsh</div>
  <nav class="main-nav">
    <a class="active" href="#">Home</a>
    <a href="#">Tv shows</a>
    <a href="#">Interviews</a>
    <a href="#">Gallery</a>
    <a href="#">Media</a>
    <a href="#">Contact Us</a>
  </nav>
</header>

<section class="hero">
  <div class="photo hero-photo" role="img" aria-label="Portrait of the doctor in glasses against a light wall"></div>
  <div class="hero-copy">
    <h1 class="hero-title">Leo Marsh</h1>
    <p class="body">Field medicine, remote rescue and emergency care come together here. Follow the shows, the lectures and the interviews, and find out how care in the wild keeps people safe far from the nearest hospital.</p>
    <a class="btn" href="#">READ MORE</a>
  </div>
  <svg class="hero-wave" width="1200" height="110" viewBox="0 0 1200 110">
    <path d="M0 40 C250 110 520 110 760 60 C940 22 1080 30 1200 70 L1200 110 L0 110 Z" fill="#fff"/>
    <path d="M0 40 C250 110 520 110 760 60 C940 22 1080 30 1200 70" fill="none" stroke="#f37122" stroke-width="5"/>
  </svg>
</section>

<section class="about">
  <div class="about-copy">
    <h2 class="section-title">About Me <span>Leonard Marsh</span></h2>
    <div class="rule"></div>
    <p class="body">Leonard Marsh, DO, EMT-P, FAWM, is an emergency physician and faculty member who trained in Florida. He serves as a medical director for rescue teams, wilderness programs and field units across the region, and teaches clinicians every year.</p>
    <p class="body">His television work brings wilderness medicine to a wide audience, with survival tips, rescue stories and honest lessons from the field for anyone who loves the outdoors.</p>
    <a class="btn" href="#">Read More</a>
  </div>
  <div class="about-portrait" role="img" aria-label="Round portrait of the doctor smiling outdoors"></div>
</section>

<section class="split tv">
  <div class="photo" role="img" aria-label="TV crew group photo in a production office"></div>
  <div class="panel panel-orange">
    <h2 class="section-title">Tv Shows</h2>
    <div class="rule rule-white"></div>
    <p class="body">From deep forests to frozen peaks, the show follows real crews as they treat injuries far from help. Each episode explains what went wrong, what went right and which simple skills can save a life when minutes count. Watch full episodes, clips and behind the scenes moments from every season here.</p>
    <a class="btn btn-outline" href="#">Read More</a>
  </div>
</section>

<section class="gallery">
  <h2 class="section-title">Photo <span>Gallery</span></h2>
  <div class="rule"></div>
  <div class="gallery-grid">
    <div class="photo g1" role="img" aria-label="Rescue vehicle parked outdoors"></div>
    <div class="photo g2" role="img" aria-label="Doctor holding a caught fish by the water"></div>
    <div class="photo g3" role="img" aria-label="Doctor with guests at a studio event"></div>
    <div class="photo g4" role="img" aria-label="Evening expedition scene"></div>
  </div>
</section>

<section class="split interviews">
  <div class="panel panel-green">
    <h2 class="section-title">My Interviews</h2>
    <div class="rule rule-white"></div>
    <p class="body">Radio hosts, podcasts and news programs regularly invite him to talk about survival, rescue medicine and staying safe outdoors. Listen to recent conversations on expedition care, disaster response and training the next generation of field clinicians, and catch up on every guest appearance in one place.</p>
    <a class="btn btn-outline" href="#">Read More</a>
  </div>
  <div class="photo" role="img" aria-label="Friends gathered at an outdoor table at dusk"></div>
</section>

<section class="media">
  <div class="photo" role="img" aria-label="Doctor photographed for a media feature"></div>
  <div class="media-copy">
    <h2 class="section-title">About Me <span>in Media</span></h2>
    <div class="rule"></div>
    <p class="body">Newspapers, magazines and websites have covered his rescues, research and teaching. Browse articles, features and profiles that share his work in wilderness and emergency medicine, with links to each story so you can read the full piece wherever it was first published.</p>
    <a class="btn" href="#">Read More</a>
  </div>
</section>

<footer class="site-footer">
  <div class="footer-brand">Leo Marsh</div>
  <nav class="footer-nav">
    <a href="#">Home</a><span class="sep">|</span>
    <a href="#">Tv shows</a><span class="sep">|</span>
    <a href="#">Interviews</a><span class="sep">|</span>
    <a href="#">gallery</a><span class="sep">|</span>
    <a href="#">Media</a><span class="sep">|</span>
    <a href="#">Contact Us</a>
  </nav>
  <p class="copyright">© Copyright 2019 - Leo Marsh All Rights Reserved.</p>
</footer>

</body>
</html>
```